Business Card Design Project

We are a construction company in Orange County, CA. We need a two sided business card. We would like the back to be our logo with web URL. Front should included Name, title, address, phone, fax and email address.

our address is
627 West Dorrance Blvd, Suite 308
Anaheim, CA 92718

Our logo files are attached.

Construction

```html
<!DOCTYPE html>
<html lang="en">
<head>
<meta charset="utf-8">
<title>Brennick Business Card</title>
<link href="https://fonts.googleapis.com/css2?family=Jost:wght@400;500;700&family=Open+Sans:wght@700&display=swap" rel="stylesheet">
<style>
  :root {
    --navy: #174a7c;
    --white: #ffffff;
    --backdrop: #e9e7e4;
    --shadow: rgba(0, 0, 0, 0.25);
  }
  * { box-sizing: border-box; margin: 0; padding: 0; }
  html, body {
    width: 1200px; height: 444px; overflow: hidden;
    background: var(--backdrop);
  }
  .canvas { position: relative; width: 1200px; height: 444px; }
  .card {
    position: absolute; top: 75px; width: 516px; height: 294px;
    box-shadow: 0 4px 10px var(--shadow);
    overflow: hidden;
  }
  .card--front { left: 70px; display: flex; }
  .card--back {
    left: 613px; background: var(--navy); color: var(--white);
    display: flex; flex-direction: column; align-items: center; justify-content: center;
    padding-top: 6px;
  }
  .front-brand {
    width: 285px; background: var(--white); color: var(--navy);
    display: flex; flex-direction: column; align-items: center; justify-content: center;
    padding-top: 14px;
  }
  .brand-name {
    font-family: "Jost", sans-serif; font-weight: 700;
    font-size: 44px; line-height: 1; letter-spacing: 0.5px;
  }
  .brand-tagline {
    font-family: "Jost", sans-serif; font-weight: 700;
    font-size: 8.5px; letter-spacing: 2.2px; margin-top: 4px;
  }
  .front-details {
    flex: 1; background: var(--navy); color: var(--white);
    padding: 50px 0 0 25px;
    font-family: "Jost", sans-serif; font-weight: 400;
  }
  .person-name { font-family: "Open Sans", sans-serif; font-weight: 700; font-size: 16px; line-height: 1.2; }
  .person-title { font-size: 13px; margin-top: 2px; }
  .contact-list { list-style: none; margin-top: 22px; font-size: 13.5px; line-height: 17.5px; }
  .contact-list li { display: flex; align-items: center; gap: 7px; }
  .contact-icon { width: 10px; height: 10px; fill: var(--white); flex: none; }
  .address { font-style: normal; margin-top: 20px; font-size: 13.5px; line-height: 17.5px; }
  .card--back .brand-name { font-size: 45px; }
  .card--back .brand-tagline { font-size: 8.5px; }
  .back-url {
    font-family: "Jost", sans-serif; font-weight: 400;
    font-size: 12.5px; letter-spacing: 2.6px; margin-top: 20px;
  }
</style>
</head>
<body>
<div class="canvas">
  <section class="card card--front">
    <div class="front-brand">
      <div class="brand-name">BRENNICK</div>
      <div class="brand-tagline">DESIGN • BUILD • DELIVER</div>
    </div>
    <div class="front-details">
      <div class="person-name">YOUR NAME</div>
      <div class="person-title">Title</div>
      <ul class="contact-list">
        <li><svg class="contact-icon" viewBox="0 0 10 10" aria-hidden="true"><path d="M2 0.5 L3.6 2.6 L2.6 3.6 Q3.6 5.8 6.4 7.4 L7.4 6.4 L9.5 8 L8.2 9.5 Q1 8 0.5 1.8 Z"/></svg>0123456789</li>
        <li><svg class="contact-icon" viewBox="0 0 10 10" aria-hidden="true"><path d="M2.5 0.5 H7.5 V3 H2.5 Z M0.5 3.5 H9.5 V8 H8 V6.5 H2 V8 H0.5 Z M2.5 7 H7.5 V9.5 H2.5 Z"/></svg>0123456789</li>
        <li><svg class="contact-icon" viewBox="0 0 10 10" aria-hidden="true"><path d="M0.5 2 H9.5 V8.5 H0.5 Z M0.5 2 L5 5.5 L9.5 2" stroke="#174a7c" stroke-width="0.8"/></svg>info@brennick.com</li>
        <li><svg class="contact-icon" viewBox="0 0 10 10" aria-hidden="true"><circle cx="5" cy="5" r="4.5"/><path d="M0.5 5 H9.5 M5 0.5 V9.5 M5 0.5 Q2 5 5 9.5 M5 0.5 Q8 5 5 9.5" stroke="#174a7c" stroke-width="0.7" fill="none"/></svg>www.brennick.com</li>
      </ul>
      <address class="address">
        627 West Dorrance Blvd<br>
        Suite 308<br>
        Anaheim, CA 92718
      </address>
    </div>
  </section>
  <section class="card card--back">
    <div class="brand-name">BRENNICK</div>
    <div class="brand-tagline">DESIGN • BUILD • DELIVER</div>
    <div class="back-url">www.brennick.com</div>
  </section>
</div>
</body>
</html>
```